Sticker to put on shipping boxes-Pet ProductDelivery

I am looking for a sticker to put on the exterior of brown shipping boxes. We deliver pet products to a local consumer base and if our clients are not home, we leave the products on the door step. We would like to place a sticker on the box so that when looking at the box the consumer knows it came from us.

Looking for a design that is not larger than about a 3x5 or 5x5? I want it large enough to stand out, yet not so large that it is overwhelming. It also does not have to be square. It can also be rectangle. It will be placed in a bottom corner.

The design need to stand out on a brown box.

Attached is our logo for you to play around with.

Take note that the file with our slogan has colors mixes up.

The words 'Premium Pet Products' should be the same gray and the word 'Pet'. And the word 'Delivered' the same color as the word 'Brisk'.

Target Market(s)

Audience is mid 20's to seniors in senior living complexes. Those interested in convince and too buy to shop for themselves.

Industry/Entity Type

Shipping

Requirements
Must have
• Color but not overwhelming.

Orange, green, blue to match the logo colors.
Should not have
• Does not need to have a lot of text. Focus more on the Brisk Paw name and logo.

```html
<!DOCTYPE html>
<html lang="en">
<head>
<meta charset="utf-8">
<title>Brisk Paw – Shipping Box Sticker</title>
<link rel="stylesheet" href="https://fonts.googleapis.com/css2?family=Ubuntu:wght@300;400&display=swap">
<style>
  :root {
    --canvas-bg: #ededed;
    --sticker-bg: #ffffff;
    --ink-dark: #6d6e71;
    --ink-light: #a7a9ac;
    --orange: #f7941d;
    --green: #8dc63f;
    --blue: #29abe2;
  }
  html, body {
    margin: 0;
    padding: 0;
    width: 1200px;
    height: 960px;
    overflow: hidden;
    background: var(--canvas-bg);
  }
  .sticker {
    position: absolute;
    left: 60px;
    top: 157px;
    width: 1080px;
    height: 645px;
    background: var(--sticker-bg);
    box-shadow: 0 4px 14px rgba(0, 0, 0, 0.18);
    overflow: hidden;
    font-family: "Ubuntu", sans-serif;
  }
  .ornament {
    position: absolute;
    border-radius: 40px;
    opacity: 0.85;
    background: linear-gradient(135deg, var(--orange) 0%, var(--green) 55%, var(--blue) 100%);
  }
  .ornament--top-left     { left: -20px;  top: -30px;  width: 200px; height: 110px; }
  .ornament--top-center   { left: 430px;  top: -30px;  width: 240px; height: 110px; }
  .ornament--top-right    { left: 810px;  top: -30px;  width: 290px; height: 110px; }
  .ornament--mid-left     { left: -30px;  top: 165px;  width: 120px; height: 260px; }
  .ornament--mid-right    { left: 945px;  top: 180px;  width: 165px; height: 240px; }
  .ornament--bottom-left  { left: -20px;  top: 480px;  width: 200px; height: 190px; }
  .ornament--bottom-center{ left: 465px;  top: 495px;  width: 240px; height: 175px; }
  .ornament--bottom-right { left: 870px;  top: 495px;  width: 230px; height: 175px; }

  .brand {
    position: absolute;
    left: 225px;
    top: 185px;
    width: 640px;
  }
  .brand__row {
    display: flex;
    align-items: center;
    gap: 28px;
  }
  .brand__dot {
    width: 96px;
    height: 96px;
    border-radius: 50%;
    background: var(--ink-dark);
    flex: none;
  }
  .brand__name {
    margin: 0;
    font-weight: 300;
    font-size: 112px;
    line-height: 1;
    color: var(--ink-dark);
    letter-spacing: -1px;
    white-space: nowrap;
  }
  .brand__tagline {
    margin: 26px 0 0;
    font-weight: 300;
    font-size: 30px;
    letter-spacing: 1px;
    color: var(--ink-light);
    white-space: nowrap;
  }
  .brand__tagline-accent {
    font-weight: 400;
    color: var(--ink-dark);
  }
</style>
</head>
<body>
  <div class="sticker">
    <div class="ornament ornament--top-left" role="img" aria-label="Orange, green and blue looping line ornament"></div>
    <div class="ornament ornament--top-center" role="img" aria-label="Orange, green and blue looping line ornament"></div>
    <div class="ornament ornament--top-right" role="img" aria-label="Orange, green and blue looping line ornament"></div>
    <div class="ornament ornament--mid-left" role="img" aria-label="Orange, green and blue looping line ornament"></div>
    <div class="ornament ornament--mid-right" role="img" aria-label="Orange, green and blue looping line ornament"></div>
    <div class="ornament ornament--bottom-left" role="img" aria-label="Orange, green and blue looping line ornament"></div>
    <div class="ornament ornament--bottom-center" role="img" aria-label="Orange, green and blue looping line ornament"></div>
    <div class="ornament ornament--bottom-right" role="img" aria-label="Orange, green and blue looping line ornament"></div>

    <div class="brand">
      <div class="brand__row">
        <span class="brand__dot"></span>
        <h1 class="brand__name">Brisk Paw</h1>
      </div>
      <p class="brand__tagline">PREMIUM PET PRODUCTS <span class="brand__tagline-accent">DELIVERED</span></p>
    </div>
  </div>
</body>
</html>
```